Boundless Volt Product design

We need a bottle design for our product. Boundless Volt is a Gaming Nootropic made to increase Energy, Focus, Reaction time, and Clarity of an eSport gamer. It will be 40 servings a bottle. Currently, all the ingredients haven't been finalized so after the competition is over we will have to work with the designer to also make an ingredients label for the back of it. For the flavor, we will call it tundra mist.

The attachments included:. The velvet outlaws picture as a font style I like for the logo.
The Z CHARGE REFRESH PICTURE IS WHAT WE WANT OUR DESIGN to look like something similar a clean and simple design that stands out!

Z Charge bottle is what our biggest competitors product looks like. The boundless volt picture as the current logo we are using but can be changed.

Overall the pictures are just some references for what I could possibly want the design to look like however, I'm open to your designer's ideas and concepts you think would make for a cool looking Gaming Nootropic product bottle design. I appreciate everyone working on this and look forward to seeing your designs have a great day!

Target Market(s)

Gamers between the ages of 18-30

Industry/Entity Type

Health And Wellness

Requirements
Must have
• Boundless Volt logo, state that it is for energy, focus, reaction, and clarity. state 40 serivngs. state flavor.

```html
<!DOCTYPE html>
<html lang="en">
<head>
<meta charset="utf-8">
<title>Boundless Volt – Tundra Mist Label</title>
<link rel="stylesheet" href="https://fonts.googleapis.com/css2?family=Oswald:wght@600&family=Saira:ital,wght@0,400;0,600;0,700;1,700;1,800&display=swap">
<style>
  :root {
    --brand-blue: #2350a5;
    --brand-blue-deep: #1f4a9c;
    --tab-blue: #2a56ab;
    --ice: #b3d6f1;
    --teal: #5ccbd9;
    --ink: #13202c;
    --white: #ffffff;
    --mist: #eef2f8;
  }
  * { margin: 0; padding: 0; box-sizing: border-box; }
  html, body { width: 1200px; height: 334px; overflow: hidden; background: var(--white); }
  .label {
    position: relative;
    width: 1200px;
    height: 334px;
    overflow: hidden;
    background: linear-gradient(to bottom, var(--white) 0, var(--white) 150px, var(--mist) 246px);
    font-family: "Saira", sans-serif;
  }
  .ice-band {
    position: absolute;
    left: 0; top: 8px;
    width: 1200px; height: 56px;
    background: linear-gradient(to bottom, var(--ice), rgba(179, 214, 241, 0.75));
  }
  .servings-tab {
    position: absolute;
    left: 734px; top: 0;
    width: 50px; height: 149px;
    background: var(--tab-blue);
    border-radius: 0 0 10px 10px;
    color: var(--white);
    text-align: center;
    font-family: "Oswald", sans-serif;
    font-weight: 600;
  }
  .servings-count { position: absolute; left: 0; right: 0; top: 98px; font-size: 24px; line-height: 1; }
  .servings-word { position: absolute; left: 0; right: 0; top: 128px; font-size: 10px; line-height: 1; }
  .brand {
    position: absolute;
    left: 428px; top: 96px;
    width: 296px;
    display: flex;
    align-items: center;
    justify-content: center;
    gap: 10px;
  }
  .brand-mark { width: 16px; height: 16px; background: var(--teal); }
  .brand-name {
    font-weight: 600;
    font-size: 28px;
    line-height: 1;
    color: var(--ink);
    letter-spacing: 0.5px;
    text-transform: uppercase;
  }
  .audience {
    position: absolute;
    left: 440px; top: 158px;
    width: 252px;
    text-align: center;
    font-style: italic;
    font-weight: 700;
    font-size: 18px;
    letter-spacing: 3px;
    color: var(--brand-blue);
  }
  .base-band {
    position: absolute;
    left: 0; top: 246px;
    width: 1200px; height: 88px;
    background: var(--brand-blue-deep);
  }
  .claims { position: absolute; left: 424px; top: 218px; display: flex; gap: 3px; }
  .claim {
    width: 42px; height: 29px;
    background: var(--brand-blue);
    clip-path: polygon(6px 0, 100% 0, calc(100% - 6px) 100%, 0 100%);
    color: var(--white);
    text-align: center;
  }
  .claim-value { display: block; font-style: italic; font-weight: 800; font-size: 18px; line-height: 20px; }
  .claim-label { display: block; font-size: 5px; line-height: 6px; text-transform: uppercase; letter-spacing: 0.3px; }
  .flavor {
    position: absolute;
    left: 602px; top: 218px;
    width: 174px; height: 29px;
    background: var(--brand-blue);
    clip-path: polygon(7px 0, 100% 0, calc(100% - 7px) 100%, 0 100%);
    color: var(--white);
    font-style: italic;
    font-weight: 800;
    font-size: 19px;
    letter-spacing: 2px;
    line-height: 29px;
    text-align: center;
  }
  .benefits {
    position: absolute;
    left: 0; top: 261px;
    width: 1200px;
    text-align: center;
    color: var(--white);
    font-weight: 700;
    font-size: 19px;
    letter-spacing: 3px;
    line-height: 1;
  }
  .legal {
    position: absolute;
    left: 0; top: 287px;
    width: 1200px;
    text-align: center;
    color: var(--white);
    font-size: 10px;
    letter-spacing: 0.4px;
    line-height: 1;
  }
</style>
</head>
<body>
  <main class="label">
    <div class="ice-band" role="img" aria-label="Band of light ice-blue slanted dashes"></div>

    <div class="servings-tab">
      <span class="servings-count">40</span>
      <span class="servings-word">servings</span>
    </div>

    <div class="brand">
      <span class="brand-mark"></span>
      <span class="brand-name">Boundless Volt</span>
    </div>

    <p class="audience">FOR E-SPORT GAMERS</p>

    <div class="base-band"></div>

    <ul class="claims" style="list-style:none">
      <li class="claim"><span class="claim-value">0</span><span class="claim-label">Sugar</span></li>
      <li class="claim"><span class="claim-value">0</span><span class="claim-label">Calories</span></li>
      <li class="claim"><span class="claim-value">0</span><span class="claim-label">Caffeine</span></li>
    </ul>

    <div class="flavor">TUNDRA MIST</div>

    <p class="benefits">ENERGY | FOCUS | REACTION | CLARITY</p>
    <p class="legal">Dietary Supplement | Net Weight 12 OZ (118g)</p>
  </main>
</body>
</html>
```